Veldmark Supplies Business Card

Professional business card that stand out to our potential customers. Front and back with clean modern design

Industry/Entity Type

Oil and gas

Contact Information for Business Card

Name, address, website , office phone and cell number

Requirements
Must have
• Editable files for each employee

```html
<!DOCTYPE html>
<html lang="en">
<head>
<meta charset="utf-8">
<title>Veldmark Supplies Business Card</title>
<link rel="stylesheet" href="https://fonts.googleapis.com/css2?family=Roboto:wght@400;500;700;900&display=swap">
<style>
  :root {
    --stage: #2e2e2e;
    --card: #242424;
    --card-front: #262626;
    --red: #e01e25;
    --cyan: #27a9d6;
    --white: #f4f4f4;
    --grey: #d8d8d8;
    --emboss: #3a3a3a;
  }
  * { margin: 0; padding: 0; box-sizing: border-box; }
  html, body { width: 1200px; height: 852px; overflow: hidden; }
  body {
    background: var(--stage);
    font-family: "Roboto", Arial, sans-serif;
    position: relative;
  }
  .card {
    position: absolute;
    top: 276px;
    width: 520px;
    height: 300px;
    border-radius: 22px;
    overflow: hidden;
    box-shadow: 0 10px 24px rgba(0,0,0,.45);
  }
  .card--front { left: 60px; background: var(--card-front); }
  .card--back { left: 620px; background: var(--card); }

  /* front */
  .front-name {
    position: absolute;
    left: 44px; top: 128px;
    display: flex; align-items: center; gap: 14px;
  }
  .brand-mark {
    width: 18px; height: 18px;
    background: var(--red);
  }
  .brand-name {
    font-weight: 900;
    font-size: 26px;
    letter-spacing: 1px;
    text-transform: uppercase;
    color: var(--white);
    line-height: 1.1;
  }
  .front-block {
    position: absolute;
    right: 60px; top: 40px;
    width: 200px; height: 200px;
    background: var(--emboss);
    border-radius: 6px;
  }

  /* back */
  .back-waves { position: absolute; inset: 0; }
  .person {
    position: absolute;
    right: 28px; top: 20px;
    text-align: right;
    color: var(--white);
  }
  .person__name { font-weight: 700; font-size: 18px; }
  .person__title { font-size: 11px; margin-top: 2px; }
  .contact {
    position: absolute;
    right: 22px; top: 152px;
    list-style: none;
    text-align: right;
    color: var(--grey);
    font-size: 12px;
    line-height: 16px;
  }
  .contact li { display: flex; justify-content: flex-end; align-items: center; gap: 6px; }
  .contact .gap { margin-top: 14px; }
  .icon { width: 10px; height: 10px; fill: var(--red); }
  .icon-space { width: 10px; }
  .back-brand {
    position: absolute;
    left: 24px; bottom: 26px;
    display: flex; align-items: center; gap: 10px;
  }
  .back-brand .brand-name { font-size: 22px; }
</style>
</head>
<body>

<section class="card card--front" aria-label="Card front">
  <div class="front-name">
    <span class="brand-mark"></span>
    <span class="brand-name">Veldmark<br>Supplies</span>
  </div>
  <div class="front-block"></div>
</section>

<section class="card card--back" aria-label="Card back">
  <svg class="back-waves" viewBox="0 0 520 300" width="520" height="300" aria-hidden="true">
    <path fill="var(--red)" d="M0,170 C110,70 280,40 400,0 L520,0 L520,60 C430,78 320,90 220,128 C130,162 50,212 0,252 Z"/>
    <path fill="none" stroke="var(--cyan)" stroke-width="7" d="M0,272 C60,220 150,170 250,135 C350,100 440,86 520,72"/>
  </svg>

  <div class="person">
    <div class="person__name">Jonas Reed Hale</div>
    <div class="person__title">Managing Director</div>
  </div>

  <ul class="contact">
    <li>415 Carrow Lane Suite 3 <span class="icon-space"></span></li>
    <li>Brayfield, Tx 79000
      <svg class="icon" viewBox="0 0 10 10"><path d="M5 0a3.5 3.5 0 0 0-3.5 3.5C1.5 6 5 10 5 10s3.5-4 3.5-6.5A3.5 3.5 0 0 0 5 0zm0 5a1.5 1.5 0 1 1 0-3 1.5 1.5 0 0 1 0 3z"/></svg></li>
    <li class="gap">(555)014-0287
      <svg class="icon" viewBox="0 0 10 10"><path d="M2 0l2 2.5-1 1.2a6 6 0 0 0 3.3 3.3l1.2-1L10 8l-1.2 1.8C4 10 0 6 .2 1.2z"/></svg></li>
    <li>sales@veldmarksupplies.com
      <svg class="icon" viewBox="0 0 10 10"><path d="M0 2h10v6H0zM0 2l5 3.5L10 2" stroke="#242424" stroke-width=".8"/></svg></li>
    <li>www.veldmarksupplies.com
      <svg class="icon" viewBox="0 0 10 10"><circle cx="5" cy="5" r="5"/></svg></li>
  </ul>

  <div class="back-brand">
    <span class="brand-mark"></span>
    <span class="brand-name">Veldmark Supplies</span>
  </div>
</section>

</body>
</html>
```